Boutique custom software development company needs new business card

Our nearly 20 year old custom software development company would like to better include the fact that we are now providing Bitcoin services. These new services are B2B include education (how to acquire and securely hold Bitcoin) and integrating Bitcoin payments into existing ecommerce sites or other existing systems. Please keep the card clean and simple. Attached is our current design and some other files. vextorial.com

Target Market(s)

businesses owners interested in long term relationship

Industry/Entity Type

Custom software development and Bitcoin

Contact Information for Business Card

Dale Parker, dale@vextorial.com, vextorial.com, (888) 555-VXTRL

Font styles to use
Other font styles liked:
• monospace

Requirements
Must have
• double-sided
Nice to have
• clean and simple
Should not have
• physical address

```html
<!DOCTYPE html>
<html lang="en">
<head>
<meta charset="utf-8">
<title>Vextorial Business Card</title>
<link rel="stylesheet" href="https://fonts.googleapis.com/css2?family=Arimo:wght@400;700&family=Open+Sans:wght@400;600&display=swap">
<style>
  :root {
    --stage: #2a2b2d;
    --card: #f1f1f0;
    --blue: #2f62a6;
    --orange: #e0691f;
    --ink: #3a3a3a;
    --rule: #b9b9b9;
  }
  * { margin: 0; padding: 0; box-sizing: border-box; }
  html, body {
    width: 1200px;
    height: 874px;
    overflow: hidden;
    background: var(--stage);
  }
  .sheet {
    width: 1200px;
    height: 874px;
    display: flex;
    flex-direction: column;
    align-items: center;
    justify-content: center;
    gap: 24px;
  }
  .card {
    width: 700px;
    height: 400px;
    background: var(--card);
    border-radius: 28px;
    position: relative;
  }

  /* Back side */
  .card--back {
    display: flex;
    flex-direction: column;
    align-items: center;
    justify-content: center;
  }
  .brand-block {
    display: flex;
    align-items: center;
    gap: 18px;
  }
  .brand-block__square {
    width: 46px;
    height: 46px;
    background: var(--blue);
  }
  .brand-block__name {
    font-family: "Arimo", sans-serif;
    font-weight: 700;
    font-size: 54px;
    letter-spacing: 1px;
    color: var(--blue);
  }
  .back-services {
    margin-top: 22px;
    font-family: "Arimo", sans-serif;
    font-size: 16px;
    letter-spacing: 1px;
    color: var(--ink);
  }
  .back-url {
    margin-top: 14px;
    font-family: "Arimo", sans-serif;
    font-size: 17px;
    letter-spacing: 5px;
    color: var(--orange);
  }

  /* Front side */
  .card--front {
    display: flex;
    align-items: center;
    padding: 0 44px 0 50px;
  }
  .identity {
    width: 300px;
    flex: none;
  }
  .identity__name {
    font-family: "Arimo", sans-serif;
    font-weight: 700;
    font-size: 44px;
    letter-spacing: 0.5px;
    color: var(--blue);
    line-height: 1;
  }
  .identity__tagline {
    margin-top: 6px;
    font-family: "Open Sans", sans-serif;
    font-size: 16px;
    letter-spacing: -0.4px;
    color: var(--blue);
  }
  .identity__services {
    margin-top: 4px;
    font-family: "Open Sans", sans-serif;
    font-weight: 600;
    font-size: 14px;
    letter-spacing: -0.2px;
    color: var(--orange);
  }
  .divider {
    width: 1.5px;
    height: 130px;
    background: var(--rule);
    margin: 0 28px 0 14px;
    flex: none;
  }
  .contact__person {
    font-family: "Arimo", sans-serif;
    font-weight: 700;
    font-size: 24px;
    letter-spacing: 0.5px;
    color: var(--blue);
    text-transform: uppercase;
    margin-bottom: 12px;
  }
  .contact__list { list-style: none; }
  .contact__item {
    display: flex;
    align-items: center;
    gap: 10px;
    font-family: "Arimo", sans-serif;
    font-size: 17px;
    color: var(--ink);
    line-height: 1.35;
  }
  .contact__icon {
    width: 12px;
    height: 12px;
    flex: none;
    fill: var(--orange);
  }
</style>
</head>
<body>
<main class="sheet">

  <section class="card card--back" aria-label="Card back">
    <div class="brand-block">
      <span class="brand-block__square"></span>
      <span class="brand-block__name">VEXTORIAL</span>
    </div>
    <p class="back-services">Custom Software &amp; Bitcoin Services</p>
    <p class="back-url">www.vextorial.com</p>
  </section>

  <section class="card card--front" aria-label="Card front">
    <div class="identity">
      <p class="identity__name">VEXTORIAL</p>
      <p class="identity__tagline">developer of custom applications</p>
      <p class="identity__services">Bitcoin education &amp; payment integration</p>
    </div>
    <span class="divider"></span>
    <div class="contact">
      <p class="contact__person">Dale Parker</p>
      <ul class="contact__list">
        <li class="contact__item">
          <svg class="contact__icon" viewBox="0 0 24 24" aria-hidden="true"><path d="M6.6 10.8a15.1 15.1 0 0 0 6.6 6.6l2.2-2.2a1 1 0 0 1 1-.25 11.4 11.4 0 0 0 3.6.57 1 1 0 0 1 1 1V20a1 1 0 0 1-1 1A17 17 0 0 1 3 4a1 1 0 0 1 1-1h3.5a1 1 0 0 1 1 1c0 1.25.2 2.45.57 3.57a1 1 0 0 1-.25 1z"/></svg>
          (888) 555-VXTRL
        </li>
        <li class="contact__item">
          <svg class="contact__icon" viewBox="0 0 24 24" aria-hidden="true"><path d="M2 5h20L12 12.5z"/><path d="M2 7.5l10 7.5 10-7.5V19H2z"/></svg>
          dale@vextorial.com
        </li>
        <li class="contact__item">
          <svg class="contact__icon" viewBox="0 0 24 24" aria-hidden="true"><circle cx="12" cy="12" r="10"/><path d="M2 12h20M12 2a15 15 0 0 1 0 20M12 2a15 15 0 0 0 0 20" fill="none" stroke="#f1f1f0" stroke-width="1.6"/></svg>
          www.vextorial.com
        </li>
      </ul>
    </div>
  </section>

</main>
</body>
</html>
```